Alaska Law Firm Needs a Sticker Design

We need a design for stickers to put on already-printed brochures. We mail the brochures to potential clients so they can learn more about accident-induced injuries, insurance claims, legal representation, and our own law firm.

One of our lawyers wrote a book that provides a helpful overview of personal injury claims. We are offering this book for free to anyone who calls and requests it. Therefore, the sticker design should include one of the following phrases, or something very similar:
a) "Still have questions? Call and request our book-- for free!"
b) "Still have questions about auto accident claims? Call and request our book today."
c) "Still have questions about filing a claim? Call and request a free copy of our book."
d) "Still have questions? Call us today to request a free copy of our book, Clear Lanes Ahead."
e) "To learn more about automobile accidents and insurance, call today and request a free copy of our book."

The sticker should be approximately 3"x3" and may be a circle, square, rectangle, or ellipsis. The sticker will be placed on the back of the folder, which is light blue. We would like the sticker to match the color scheme of our website and the folder.

I will upload an image of the book cover as soon as I obtain it.

Law Firm

Font styles to use
Serif
Sans Serif

Requirements
Should not have
• Bright colors that aren't already used in the folder design. e.g. no bright orange, pink, chartreuse, turquoise, yellow, red.

```html
<!DOCTYPE html>
<html lang="en">
<head>
<meta charset="utf-8">
<title>Free Book Sticker</title>
<link rel="stylesheet" href="https://fonts.googleapis.com/css2?family=Cinzel:wght@400;500&family=Arimo&display=swap">
<style>
  :root {
    --navy: #143f6b;
    --navy-edge: #1b4a7e;
    --pale: #d6e4f5;
    --ink-light: #e2ecf8;
    --phone-ink: #1d4b7b;
    --page: #ffffff;
  }
  * { margin: 0; padding: 0; box-sizing: border-box; }
  html, body { width: 1200px; height: 701px; overflow: hidden; background: var(--page); }
  .sticker { position: relative; width: 1200px; height: 701px; }
  .sticker-frame { position: absolute; inset: 0; }
  .headline, .subline, .offer {
    position: absolute; left: 0; width: 1114px; text-align: center;
    font-family: "Cinzel", "Times New Roman", serif; color: var(--ink-light);
    font-weight: 400; white-space: nowrap;
  }
  .headline { top: 116px; font-size: 44px; letter-spacing: 1px; font-variant: small-caps; }
  .subline  { top: 184px; font-size: 33px; letter-spacing: 1px; font-variant: small-caps; }
  .offer    { top: 236px; font-size: 60px; letter-spacing: 3px; }
  .book-cover {
    position: absolute; left: 500px; top: 337px; width: 118px; height: 190px;
    background: linear-gradient(180deg, #f4f6f8 0%, #e9eef2 22%, #9cc28a 60%, #6f9c5b 85%, #1e2a55 100%);
    box-shadow: 6px 4px 0 #c9cdd2, 8px 8px 10px rgba(0,0,0,0.35);
  }
  .phone {
    position: absolute; left: 416px; top: 569px; width: 285px; text-align: center;
    font-family: "Arimo", Arial, sans-serif; font-size: 28px; color: var(--phone-ink);
  }
</style>
</head>
<body>
  <main class="sticker">
    <svg class="sticker-frame" width="1200" height="701" viewBox="0 0 1200 701" aria-hidden="true">
      <defs>
        <path id="bracket-shape" d="M557,42 C575,60 595,72 630,76 L945,78 C985,78 995,95 990,120 C985,135 990,150 1000,170 L1000,330 C1005,345 1015,355 1024,360 C1015,365 1005,375 1000,390 L1000,560 C990,580 985,595 990,610 C995,635 985,650 945,650 L630,652 C595,656 575,668 557,686 C539,668 519,656 484,652 L169,650 C129,650 119,635 124,610 C129,595 124,580 114,560 L114,390 C109,375 99,365 90,360 C99,355 109,345 114,330 L114,170 C124,150 129,135 124,120 C119,95 129,78 169,78 L484,76 C519,72 539,60 557,42 Z"/>
      </defs>
      <use href="#bracket-shape" fill="none" stroke="var(--navy-edge)" stroke-width="26" stroke-linejoin="round"/>
      <use href="#bracket-shape" fill="var(--navy)" stroke="var(--pale)" stroke-width="19" stroke-linejoin="round"/>
      <circle class="book-ring" cx="557" cy="424" r="124" fill="none" stroke="var(--pale)" stroke-width="4"/>
      <circle class="book-disc" cx="557" cy="424" r="107" fill="var(--pale)"/>
      <polygon class="phone-ribbon" points="416,555 701,555 687,584 701,613 416,613 430,584" fill="var(--pale)"/>
    </svg>

    <h1 class="headline">Still have questions?</h1>
    <p class="subline">Call and request our book</p>
    <p class="offer">FOR FREE</p>

    <div class="book-cover" role="img" aria-label="Cover of the book Clear Lanes Ahead by Daniel R. Marsh, showing a family photo outdoors"></div>

    <p class="phone">(907) 555- 0142</p>
  </main>
</body>
</html>
```